Business Card Design for Marketing Firm

Looking for business card design for higher end marketing firm. Clean but impressionable/trendy. We are a marketing firm that represents manufacturers in the foodservice equipment and supply industry. Our customers are end users such has hotels, restaurants, country clubs, convention centers and casinos as well as distributors of restaurants supplies and equipment, and manufacturers of foodservice equipment and supplies.
Target Market(s)
Hotels, Restaurants, Supply & Equipment Distributors, Foodservice Manufacturers
Industry/Entity Type
Foodservice/Hospitality
Contact Information for Business Card
Name, Title, Contact Number, Email, Website, Social Media, Address
Requirements
Must have
- Clean & Simple but Serious and Impressionable

```html
<!DOCTYPE html>
<html lang="en">
<head>
<meta charset="utf-8">
<title>Meridian Hospitality Reps – Business Card</title>
<link href="https://fonts.googleapis.com/css2?family=Montserrat:wght@400;500;700&display=swap" rel="stylesheet">
<style>
  :root {
    --backdrop: #2a2a2b;
    --card: #ffffff;
    --navy: #2b2a80;
    --ink: #1c1c2a;
  }
  * { box-sizing: border-box; margin: 0; padding: 0; }
  html, body { width: 1200px; height: 900px; overflow: hidden; }
  body {
    background: var(--backdrop);
    position: relative;
    font-family: "Montserrat", Arial, sans-serif;
    color: var(--ink);
  }
  .card {
    position: absolute;
    width: 640px;
    height: 366px;
    background: var(--card);
    border-radius: 22px;
    overflow: hidden;
  }
  .card--front { left: 80px; top: 70px; }
  .card--back { left: 480px; top: 464px; }

  .brand-name {
    font-family: "Montserrat", Arial, sans-serif;
    font-weight: 500;
    color: var(--navy);
    text-transform: uppercase;
    letter-spacing: 0.06em;
    white-space: nowrap;
  }

  /* Front */
  .front-brand {
    position: absolute;
    left: 0; right: 0; top: 138px;
    text-align: center;
    font-size: 26px;
  }
  .social-row {
    position: absolute;
    left: 0; right: 0; top: 258px;
    display: flex;
    justify-content: center;
    gap: 8px;
  }
  .social-dot {
    width: 13px; height: 13px;
    border-radius: 50%;
    background: var(--navy);
  }

  /* Back */
  .back-brand {
    position: absolute;
    left: 40px; top: 52px;
    font-size: 19px;
  }
  .holder-name {
    position: absolute;
    left: 40px; top: 152px;
    font-weight: 700;
    font-size: 24px;
    color: var(--navy);
  }
  .holder-title {
    position: absolute;
    left: 48px; top: 184px;
    font-size: 12px;
  }
  .address {
    position: absolute;
    left: 56px; top: 208px;
    font-size: 12px;
    line-height: 1.45;
  }
  .contact-list {
    position: absolute;
    left: 56px; top: 252px;
    list-style: none;
    font-size: 12.5px;
  }
  .contact-list li {
    display: flex;
    align-items: center;
    gap: 10px;
    height: 21px;
  }
  .contact-list svg { width: 14px; height: 14px; fill: var(--navy); flex: none; }
  .back-mark {
    position: absolute;
    right: 36px; top: 120px;
    font-size: 54px;
    letter-spacing: 0.02em;
  }
</style>
</head>
<body>
  <section class="card card--front" aria-label="Card front">
    <div class="brand-name front-brand">Meridian Hospitality Reps</div>
    <div class="social-row" aria-label="Social media links">
      <span class="social-dot" role="img" aria-label="Social network one"></span>
      <span class="social-dot" role="img" aria-label="Social network two"></span>
      <span class="social-dot" role="img" aria-label="Social network three"></span>
    </div>
  </section>

  <section class="card card--back" aria-label="Card back">
    <div class="brand-name back-brand">Meridian Hospitality Reps</div>
    <div class="holder-name">Jonah Keller</div>
    <div class="holder-title">Owner</div>
    <div class="address">418 Harbor Ave. Suite 210<br>Bay City, OR 97107</div>
    <ul class="contact-list">
      <li>
        <svg viewBox="0 0 16 16" aria-hidden="true"><path d="M2 6c0-2 2-3 6-3s6 1 6 3v1h-3V6H5v1H2zM4 8h8l2 5H2z"/></svg>
        (555) 214-0387
      </li>
      <li>
        <svg viewBox="0 0 16 16" aria-hidden="true"><path d="M4 1h8v14H4zM5.5 2.5v9h5v-9z"/></svg>
        (555) 214-0387
      </li>
      <li>
        <svg viewBox="0 0 16 16" aria-hidden="true"><path d="M1 3h14v10H1zM2 4.5v.6l6 4 6-4v-.6z"/></svg>
        info@meridianhospitality.com
      </li>
      <li>
        <svg viewBox="0 0 16 16" aria-hidden="true"><circle cx="8" cy="8" r="7"/></svg>
        www.meridianhospitality.com
      </li>
    </ul>
    <div class="brand-name back-mark">Meridian</div>
  </section>
</body>
</html>
```